Elevating our current Business Card Design

We want to elevate our current business card with a new design to look like a zenith 300 company. We are a premium lubricant distributor (oil and grease).
We need 2 versions, version 1 is as per the uploaded a copy of our current business card with the English version.
For our Chinese version we need to use the front to be English in English and have the back of the card designed exactly like the front for all info to be in Chinese.
The design template needs to be such that we can amend the template with adding different information for each person's card.
The background colour of the card can be changed- we just need to clearly see all information on the card and logos.
The QJR and Ember steady logos cannot have any colour or display changes- only use the logos attached.
All logos need to be included and all information from the attached current card

```html
<!DOCTYPE html>
<html lang="en">
<head>
<meta charset="utf-8">
<title>Northgate Lubricant Distributors – Business Card</title>
<link rel="stylesheet" href="https://fonts.googleapis.com/css2?family=Open+Sans:wght@400;700;800&display=swap">
<style>
  :root {
    --stage: #222222;
    --card: #ffffff;
    --red: #e8262a;
    --ink: #1e1e1e;
    --badge: #d6d6d6;
    --badge-soft: #ececec;
  }
  * { box-sizing: border-box; margin: 0; padding: 0; }
  html, body { width: 1200px; height: 780px; overflow: hidden; }
  body {
    background: var(--stage);
    font-family: "Open Sans", Arial, sans-serif;
    color: var(--ink);
    position: relative;
  }
  .card {
    position: absolute;
    top: 235px;
    width: 540px;
    height: 310px;
    background: var(--card);
    border-radius: 16px;
    overflow: hidden;
  }
  .card--back { left: 40px; }
  .card--front { left: 620px; }

  /* company name set in the card's text font */
  .company-name {
    display: flex;
    align-items: center;
    color: var(--red);
    font-weight: 700;
    line-height: 1;
    white-space: nowrap;
  }
  .company-name__square { background: var(--red); flex: none; }
  .card--back .company-name {
    position: absolute; left: 28px; top: 28px; font-size: 24px; gap: 9px;
  }
  .card--back .company-name__square { width: 12px; height: 12px; }
  .card--front .company-name {
    position: absolute; left: 0; right: 0; top: 128px;
    justify-content: center; font-size: 52px; gap: 16px;
  }
  .card--front .company-name__square { width: 24px; height: 24px; }

  /* contact block */
  .address {
    position: absolute; left: 28px; top: 80px;
    font-size: 12px; line-height: 16px;
  }
  .contacts {
    position: absolute; left: 28px; top: 120px;
    list-style: none; font-size: 12px; line-height: 17px;
  }
  .contacts li { display: flex; align-items: center; gap: 7px; }
  .contacts svg { width: 11px; height: 11px; fill: none; stroke: var(--red); stroke-width: 1.6; flex: none; }

  /* name */
  .person { position: absolute; right: 34px; top: 150px; text-align: right; }
  .person__name { color: var(--red); font-weight: 800; font-size: 30px; line-height: 1.05; }
  .person__role { font-size: 14px; margin-top: 2px; }
  .edge-tab {
    position: absolute; right: 0; top: 158px; width: 18px; height: 46px;
    background: var(--red);
  }

  /* credentials row: plain badge shapes */
  .credentials {
    position: absolute; left: 28px; bottom: 18px;
    display: flex; align-items: flex-end; gap: 14px;
  }
  .badge-round {
    width: 48px; height: 48px; border-radius: 50%; background: var(--badge);
  }
  .badge-box {
    width: 200px; height: 62px; border-radius: 6px; background: var(--badge-soft);
  }
</style>
</head>
<body>

  <section class="card card--back" aria-label="Card back with contact details">
    <div class="company-name"><span class="company-name__square"></span>Northgate</div>

    <p class="address">48 Freight Way<br>Ashdale, WA 6190</p>

    <ul class="contacts">
      <li><svg viewBox="0 0 12 12"><path d="M2 1h2l1 3-1.5 1a6 6 0 0 0 3 3L8 7l3 1v2a1 1 0 0 1-1 1A9 9 0 0 1 1 2a1 1 0 0 1 1-1z"/></svg>1300 472 615</li>
      <li><svg viewBox="0 0 12 12"><rect x="3" y="1" width="6" height="10" rx="1"/></svg>+61 400 218 764</li>
      <li><svg viewBox="0 0 12 12"><rect x="1" y="4" width="10" height="7" rx="1"/><path d="M3 4V1h6v3"/></svg>+61 8 9400 2351</li>
      <li><svg viewBox="0 0 12 12"><circle cx="6" cy="6" r="5"/><path d="M1 6h10M6 1c-2 3-2 7 0 10M6 1c2 3 2 7 0 10"/></svg>www.northgatelube.com</li>
      <li><svg viewBox="0 0 12 12"><rect x="1" y="2.5" width="10" height="7" rx="1"/><path d="M1 3l5 4 5-4"/></svg>m.castell@northgatelube.com</li>
    </ul>

    <div class="person">
      <p class="person__name">Marina Castell</p>
      <p class="person__role">Administration Executive</p>
    </div>
    <div class="edge-tab"></div>

    <div class="credentials">
      <div class="badge-round" role="img" aria-label="Ember steady network member badge"></div>
      <div class="badge-box" role="img" aria-label="Distributor and partner lubricant brand badge"></div>
      <div class="badge-round" role="img" aria-label="QJR certification badge"></div>
      <div class="badge-round" role="img" aria-label="QJR certification badge"></div>
      <div class="badge-round" role="img" aria-label="QJR certification badge"></div>
    </div>
  </section>

  <section class="card card--front" aria-label="Card front">
    <div class="company-name"><span class="company-name__square"></span>Northgate</div>
  </section>

</body>
</html>
```